VOMRA Pty Ltd Business Card

Looking for a simple yet eye-catching double-sided business card design using my company logo on one side and contact details on the other.

Target Market(s)

Government

Industry/Entity Type

Communication Systems Engineering

Contact Information for Business Card

VOMRA Pty Ltd

Requirements
Nice to have
• Would be great to have a QR code so details can be scanned into contacts

```html
<!DOCTYPE html>
<html lang="en">
<head>
<meta charset="utf-8">
<title>VOMRA Pty Ltd Business Card</title>
<link rel="stylesheet" href="https://fonts.googleapis.com/css2?family=Figtree:wght@400;600;700&display=swap">
<style>
  :root {
    --page: #e3e3e1;
    --slate: #343d44;
    --slate-light: #47515a;
    --paper: #f1f1f1;
    --paper-shade: #e6e6e6;
    --ink: #2e363c;
    --ink-soft: #5d6369;
    --light-text: #f2efed;
  }
  * { margin: 0; padding: 0; box-sizing: border-box; }
  html, body { width: 1200px; height: 1200px; overflow: hidden; }
  body {
    background: var(--page);
    font-family: "Figtree", sans-serif;
    position: relative;
  }
  .card {
    position: absolute;
    left: 234px;
    width: 732px;
    height: 418px;
    overflow: hidden;
  }
  .card-front {
    top: 160px;
    background: linear-gradient(200deg, var(--slate-light) 0%, var(--slate) 55%, #303940 100%);
    display: flex;
    align-items: center;
    justify-content: center;
    gap: 26px;
  }
  .brand-dot {
    width: 96px;
    height: 96px;
    border-radius: 50%;
    background: var(--light-text);
  }
  .brand-name {
    font-weight: 600;
    color: var(--light-text);
    font-size: 124px;
    line-height: 1;
    letter-spacing: 2px;
  }
  .card-back {
    top: 632px;
    background: linear-gradient(200deg, #f5f5f5 0%, var(--paper) 45%, var(--paper-shade) 100%);
  }
  .back-brand {
    position: absolute;
    left: 54px;
    top: 56px;
    display: flex;
    align-items: center;
    gap: 14px;
  }
  .back-brand .brand-dot {
    width: 48px;
    height: 48px;
    background: var(--ink);
  }
  .back-brand .brand-name {
    color: var(--ink);
    font-size: 62px;
    letter-spacing: 1px;
  }
  .person {
    position: absolute;
    right: 54px;
    top: 190px;
    text-align: right;
  }
  .person-name {
    font-weight: 700;
    font-size: 31px;
    color: var(--ink);
  }
  .person-title {
    font-size: 20px;
    color: var(--ink-soft);
    margin-top: 6px;
  }
  .divider {
    position: absolute;
    left: 54px;
    top: 242px;
    width: 418px;
    height: 2px;
    background: var(--ink);
  }
  .contact-list {
    position: absolute;
    left: 54px;
    top: 262px;
    list-style: none;
  }
  .contact-item {
    display: flex;
    align-items: center;
    gap: 10px;
    font-size: 20px;
    color: var(--ink);
    height: 28px;
  }
  .contact-item svg { width: 17px; height: 17px; fill: var(--ink); flex: none; }
  .address-band {
    position: absolute;
    left: 0; right: 0; bottom: 0;
    height: 50px;
    background: var(--slate);
    color: var(--light-text);
    font-size: 19px;
    display: flex;
    align-items: center;
    justify-content: center;
    letter-spacing: 0.2px;
  }
</style>
</head>
<body>
  <section class="card card-front">
    <span class="brand-dot"></span>
    <span class="brand-name">VOMRA</span>
  </section>

  <section class="card card-back">
    <div class="back-brand">
      <span class="brand-dot"></span>
      <span class="brand-name">VOMRA</span>
    </div>

    <div class="person">
      <div class="person-name">Marcus Ellery</div>
      <div class="person-title">Founder &amp; Director</div>
    </div>

    <div class="divider"></div>

    <ul class="contact-list">
      <li class="contact-item">
        <svg viewBox="0 0 24 24" aria-hidden="true"><path d="M6.6 10.8a15.1 15.1 0 0 0 6.6 6.6l2.2-2.2a1 1 0 0 1 1-.25 11.4 11.4 0 0 0 3.6.57 1 1 0 0 1 1 1V20a1 1 0 0 1-1 1A17 17 0 0 1 3 4a1 1 0 0 1 1-1h3.5a1 1 0 0 1 1 1c0 1.25.2 2.45.57 3.57a1 1 0 0 1-.25 1z"/></svg>
        (402)-555-0147
      </li>
      <li class="contact-item">
        <svg viewBox="0 0 24 24" aria-hidden="true"><path d="M2 5h20v14H2z M4 7v.4l8 5.2 8-5.2V7z" fill-rule="evenodd"/></svg>
        admin@vomra.com.au
      </li>
      <li class="contact-item">
        <svg viewBox="0 0 24 24" aria-hidden="true"><path d="M12 2a10 10 0 1 0 0 20 10 10 0 0 0 0-20zm6.9 9h-3a15.5 15.5 0 0 0-1.3-5.6A8 8 0 0 1 18.9 11zM12 4.1c.9 1.2 1.7 3.7 1.9 6.9h-3.8c.2-3.2 1-5.7 1.9-6.9zM9.4 5.4A15.5 15.5 0 0 0 8.1 11h-3a8 8 0 0 1 4.3-5.6zM5.1 13h3a15.5 15.5 0 0 0 1.3 5.6A8 8 0 0 1 5.1 13zm6.9 6.9c-.9-1.2-1.7-3.7-1.9-6.9h3.8c-.2 3.2-1 5.7-1.9 6.9zm2.6-1.3a15.5 15.5 0 0 0 1.3-5.6h3a8 8 0 0 1-4.3 5.6z"/></svg>
        www.vomra.com.au
      </li>
    </ul>

    <div class="address-band">47-49 Harlow Lane Redfield NSW 2031 Australia</div>
  </section>
</body>
</html>
```